Maple Grove Schools | brand new stationery!

We need stationery design with our new logo! Our company updated it's name and image and we like to incorporate the new one on our stationery, business cards and email signature. We are looking for fresh, new ideas!
Industry: Childcare, Elementary and Middle School
Company Name: Maple Grove Schools
Tagline: Bright Futures Start Here
Main colors: Blue, white and a little yellow
Star shape is something new for us! Do you see a way to incorporate it as a design element?

```html
<!DOCTYPE html>
<html lang="en">
<head>
<meta charset="utf-8">
<title>Maple Grove Schools – Business Cards</title>
<link href="https://fonts.googleapis.com/css2?family=Urbanist:wght@500;800&family=Poppins:wght@400;500&family=Raleway:wght@400&display=swap" rel="stylesheet">
<style>
  :root {
    --backdrop: #b58a47;
    --card: #ffffff;
    --navy: #0d1f7a;
    --ink: #222222;
    --muted: #3a3a3a;
  }
  * { margin: 0; padding: 0; box-sizing: border-box; }
  html, body { width: 1200px; height: 914px; overflow: hidden; }
  body { background: var(--backdrop); position: relative; font-family: "Raleway", sans-serif; }

  .card {
    position: absolute;
    left: 525px;
    width: 505px;
    height: 310px;
    background: var(--card);
    border-radius: 22px;
    box-shadow: 0 8px 22px rgba(60, 35, 5, 0.28);
  }
  .card--front { top: 116px; }
  .card--back { top: 468px; }

  /* Front */
  .front-mark {
    position: absolute;
    left: 220px; top: 40px;
    width: 80px; height: 80px;
    border-radius: 50%;
    background: var(--navy);
  }
  .front-name {
    position: absolute;
    left: 0; right: 0; top: 132px;
    text-align: center;
    font-family: "Urbanist", sans-serif;
    font-weight: 800;
    font-size: 38px;
    line-height: 42px;
    color: var(--ink);
  }
  .front-tagline {
    position: absolute;
    left: 0; right: 0; top: 242px;
    text-align: center;
    font-family: "Poppins", sans-serif;
    font-weight: 500;
    font-size: 24px;
    color: var(--muted);
  }

  /* Back */
  .back-name {
    position: absolute;
    left: 19px; top: 18px;
    font-family: "Urbanist", sans-serif;
    font-weight: 800;
    font-size: 36px;
    line-height: 40px;
    color: var(--ink);
  }
  .person {
    position: absolute;
    left: 22px; top: 122px;
  }
  .person__name {
    font-family: "Urbanist", sans-serif;
    font-weight: 800;
    font-size: 25px;
    line-height: 28px;
    color: var(--navy);
    text-transform: uppercase;
  }
  .person__role {
    font-size: 15px;
    color: var(--muted);
    margin-top: 2px;
  }
  .contacts {
    position: absolute;
    left: 22px; top: 180px;
    list-style: none;
  }
  .contacts li {
    display: flex;
    align-items: center;
    gap: 10px;
    font-size: 14.5px;
    color: var(--muted);
    height: 22px;
  }
  .contacts svg { width: 12px; height: 12px; fill: var(--navy); flex: none; }
  .address {
    position: absolute;
    left: 22px; top: 254px;
    font-size: 14.5px;
    line-height: 22px;
    color: var(--muted);
    font-style: normal;
  }
  .back-mark {
    position: absolute;
    left: 268px; top: 52px;
    width: 210px; height: 210px;
    border-radius: 50%;
    background: var(--navy);
  }
</style>
</head>
<body>
  <section class="card card--front" aria-label="Business card front">
    <div class="front-mark"></div>
    <h1 class="front-name">Maple Grove<br>Schools</h1>
    <p class="front-tagline">Bright Futures Start Here</p>
  </section>

  <section class="card card--back" aria-label="Business card back">
    <h2 class="back-name">Maple Grove<br>Schools</h2>
    <div class="person">
      <p class="person__name">Daniel Whitford</p>
      <p class="person__role">Managing Director</p>
    </div>
    <ul class="contacts">
      <li>
        <svg viewBox="0 0 24 24" aria-hidden="true"><path d="M6.6 10.8a15.1 15.1 0 0 0 6.6 6.6l2.2-2.2a1 1 0 0 1 1-.25 11.4 11.4 0 0 0 3.6.57 1 1 0 0 1 1 1V20a1 1 0 0 1-1 1A17 17 0 0 1 3 4a1 1 0 0 1 1-1h3.5a1 1 0 0 1 1 1c0 1.25.2 2.45.57 3.57a1 1 0 0 1-.25 1z"/></svg>
        055-310 482 617
      </li>
      <li>
        <svg viewBox="0 0 24 24" aria-hidden="true"><path d="M2 5h20v14H2z M4 7v.5l8 5.5 8-5.5V7l-8 5.5z" fill-rule="evenodd"/></svg>
        hello@maplegrovemail.com
      </li>
      <li>
        <svg viewBox="0 0 24 24" aria-hidden="true"><path d="M12 2a10 10 0 1 0 0 20 10 10 0 0 0 0-20zm0 2a8 8 0 0 1 6.9 4H15c-.5-1.5-1.2-2.8-2-3.9A8 8 0 0 1 12 4zm-3 6h6a14 14 0 0 1 0 4H9a14 14 0 0 1 0-4zm-4.7 0H7a16 16 0 0 0 0 4H4.3a8 8 0 0 1 0-4zm12.7 0h2.7a8 8 0 0 1 0 4H17a16 16 0 0 0 0-4zM5.1 16H9c.5 1.5 1.1 2.8 1.9 3.9A8 8 0 0 1 5.1 16zm9.9 0h3.9a8 8 0 0 1-5.8 3.9c.8-1.1 1.4-2.4 1.9-3.9z"/></svg>
        www.maplegroveschools.org
      </li>
    </ul>
    <address class="address">18 Orchard Lane<br>Fairview, 30518</address>
    <div class="back-mark"></div>
  </section>
</body>
</html>
```